Ostrevan Capital LLC

Need Professional Business cards for New Investment Fund

Target Market(s)

High Quality investors

Industry/Entity Type

Financial

Contact Information for Business Card

Phone Number +1 555 284 6190
Name Lukas Varenko
Title Fund Manager
email lv@FundOstrevan.com
Website www.FundOstrevan.com

Colors

Designer to choose colors to be used in the design.

Requirements
Must have
• Must have our Logo and all of the above. Must be made so lettering and loge can be raised

```html
<!DOCTYPE html>
<html lang="en">
<head>
<meta charset="utf-8">
<title>Ostrevan Capital LLC — Business Card</title>
<link rel="stylesheet" href="https://fonts.googleapis.com/css2?family=Lato:wght@400;700&display=swap">
<style>
  :root {
    --backdrop: #3b3431;
    --card: #0c0c0c;
    --card-edge: #1a1a1a;
    --accent-green: #2fd42a;
    --text-grey: #b9b9b9;
    --divider: #262626;
    --silver: #d9d9d9;
  }
  * { margin: 0; padding: 0; box-sizing: border-box; }
  html, body {
    width: 1200px;
    height: 844px;
    overflow: hidden;
    background: var(--backdrop);
    font-family: "Lato", sans-serif;
  }
  .canvas {
    position: relative;
    width: 1200px;
    height: 844px;
    display: flex;
    align-items: center;
    justify-content: center;
    gap: 60px;
  }
  .card {
    position: relative;
    width: 520px;
    height: 300px;
    background: var(--card);
    border: 1px solid var(--card-edge);
    border-radius: 3px;
  }

  /* Front side */
  .card--front { display: flex; }
  .brand-panel {
    width: 200px;
    height: 100%;
    display: flex;
    align-items: center;
    justify-content: center;
    border-right: 1px solid var(--divider);
  }
  .brand-name {
    display: flex;
    align-items: center;
    gap: 9px;
    font-size: 22px;
    font-weight: 700;
    letter-spacing: 1.5px;
    color: var(--accent-green);
    white-space: nowrap;
  }
  .brand-mark {
    width: 12px;
    height: 12px;
    flex: none;
    background: var(--accent-green);
  }
  .contact-panel {
    flex: 1;
    padding: 62px 0 0 34px;
  }
  .contact-name {
    font-size: 21px;
    font-weight: 700;
    letter-spacing: 1px;
    text-transform: uppercase;
    color: var(--accent-green);
  }
  .contact-title {
    margin-top: 2px;
    font-size: 14px;
    color: var(--text-grey);
  }
  .contact-list {
    list-style: none;
    margin-top: 26px;
  }
  .contact-item {
    display: flex;
    align-items: center;
    gap: 10px;
    font-size: 15px;
    line-height: 22px;
    color: var(--text-grey);
  }
  .contact-icon { width: 12px; height: 12px; flex: none; }

  /* Back side */
  .card--back {
    display: flex;
    align-items: center;
    justify-content: center;
  }
  .card--back .brand-name {
    font-size: 32px;
    gap: 12px;
    color: var(--silver);
  }
  .card--back .brand-mark {
    width: 17px;
    height: 17px;
    background: var(--silver);
  }
</style>
</head>
<body>
<main class="canvas">
  <section class="card card--front" aria-label="Business card front">
    <div class="brand-panel">
      <div class="brand-name"><span class="brand-mark"></span>Ostrevan</div>
    </div>
    <div class="contact-panel">
      <h1 class="contact-name">Lukas Varenko</h1>
      <p class="contact-title">Fund Manager</p>
      <ul class="contact-list">
        <li class="contact-item">
          <svg class="contact-icon" viewBox="0 0 12 12" aria-hidden="true"><path fill="#2fd42a" d="M1 3c0-1 1-2 2-2h6c1 0 2 1 2 2v1H8V3H4v1H1zM2 5h8l1 6H1z"/></svg>
          +1 555 284 6190
        </li>
        <li class="contact-item">
          <svg class="contact-icon" viewBox="0 0 12 12" aria-hidden="true"><rect x="0.5" y="2" width="11" height="8" fill="#2fd42a"/><path d="M0.5 2.5 6 6.5l5.5-4" stroke="#0c0c0c" fill="none"/></svg>
          lv@FundOstrevan.com
        </li>
        <li class="contact-item">
          <svg class="contact-icon" viewBox="0 0 12 12" aria-hidden="true"><circle cx="6" cy="6" r="5.5" fill="#2fd42a"/><path d="M0.5 6h11M6 0.5c-3 3-3 8 0 11M6 0.5c3 3 3 8 0 11" stroke="#0c0c0c" fill="none" stroke-width="0.8"/></svg>
          www.FundOstrevan.com
        </li>
      </ul>
    </div>
  </section>

  <section class="card card--back" aria-label="Business card back">
    <div class="brand-name"><span class="brand-mark"></span>Ostrevan</div>
  </section>
</main>
</body>
</html>
```